Upmarket Dessert Lounge needs a Business Card Design

We are an upmarket dessert lounge needing a business card to match our image.

We want something that is simple yet beautiful, feminine, classy, sophisticated and elegant. We want it to stand out and don't mind if it is bold.

The design should include our logo and colours of red or maroon with gold highlights. We don't mind if black is used.

Marlow & Quince

Target Market(s)

For those who like to indulge or treat themselves and give in to their temptations on good quality desserts.

Industry/Entity Type

Business

Requirements
Must have
• Must include our logo and our name

Marlow & Quince

M & Q

```html
<!DOCTYPE html>
<html lang="en">
<head>
<meta charset="utf-8">
<title>Marlow &amp; Quince — Business Card</title>
<link rel="stylesheet" href="https://fonts.googleapis.com/css2?family=Tinos:wght@400;700&display=swap">
<style>
  :root {
    --maroon: #7b1416;
    --cream: #f6d9b0;
    --card: #ffffff;
    --ink-soft: #5a5a5a;
    --ink: #333333;
    --stage: #ece8e3;
    --rule: #9a9a9a;
  }
  * { box-sizing: border-box; margin: 0; padding: 0; }
  html, body { width: 1200px; height: 417px; overflow: hidden; }
  body {
    background: var(--stage);
    font-family: "Tinos", "Times New Roman", serif;
    position: relative;
  }
  .card {
    position: absolute;
    background: var(--card);
    width: 515px;
    box-shadow: 0 2px 6px rgba(0,0,0,0.18);
    overflow: hidden;
  }
  .card--front { left: 54px; top: 61px; height: 310px; }
  .card--back  { left: 629px; top: 61px; height: 294px; }

  .wordmark {
    position: absolute;
    color: var(--maroon);
    font-weight: 400;
    font-size: 28px;
    letter-spacing: 0.5px;
    white-space: nowrap;
    transform: translate(-50%, -50%);
  }
  .card--front .wordmark { left: 160px; top: 135px; font-size: 26px; }
  .card--back .wordmark { left: 257px; top: 135px; font-size: 32px; }

  .divider {
    position: absolute;
    left: 326px; top: 74px;
    width: 1px; height: 145px;
    background: linear-gradient(to bottom, transparent, var(--rule) 15%, var(--rule) 85%, transparent);
  }
  .contact-block {
    position: absolute;
    left: 343px; top: 80px;
  }
  .contact-block .person-name {
    color: var(--maroon);
    font-weight: 700;
    font-size: 18px;
    line-height: 20px;
    text-transform: uppercase;
  }
  .contact-block .person-title {
    color: var(--ink-soft);
    font-size: 13px;
    line-height: 18px;
    margin-bottom: 10px;
  }
  .contact-list { list-style: none; }
  .contact-list li {
    display: flex;
    align-items: center;
    gap: 7px;
    color: var(--ink);
    font-size: 13.5px;
    line-height: 20.5px;
  }
  .contact-list svg { width: 10px; height: 10px; flex: none; fill: var(--maroon); }

  .footer-band { position: absolute; left: 0; bottom: 0; width: 515px; height: 80px; }
  .footer-band .band-cream { fill: var(--cream); }
  .footer-band .band-maroon { fill: var(--maroon); }
  .address {
    position: absolute;
    left: 60px; top: 265px;
    color: #ffffff;
    font-size: 13px;
  }

  .web-address {
    position: absolute;
    left: 0; right: 0; top: 248px;
    text-align: center;
    color: var(--ink-soft);
    font-size: 12.5px;
    letter-spacing: 3px;
  }
</style>
</head>
<body>

  <section class="card card--front">
    <div class="wordmark">MARLOW &amp; QUINCE</div>

    <div class="divider"></div>

    <div class="contact-block">
      <p class="person-name">Your Name</p>
      <p class="person-title">Title</p>
      <ul class="contact-list">
        <li>
          <svg viewBox="0 0 10 10" aria-hidden="true"><path d="M2 0.5 L3.6 2.6 L2.7 3.6 Q3.6 5.6 6.4 7.3 L7.4 6.4 L9.5 8 L8.3 9.5 Q3.5 8.8 0.5 1.7 Z"/></svg>
          +2348100457321
        </li>
        <li>
          <svg viewBox="0 0 10 10" aria-hidden="true"><path d="M2.5 0 H7.5 V10 H2.5 Z M3.3 1 V7 H6.7 V1 Z M4.5 8 H5.5 V9 H4.5 Z" fill-rule="evenodd"/></svg>
          +2348100457321
        </li>
        <li>
          <svg viewBox="0 0 10 10" aria-hidden="true"><path d="M0 2 H10 V8.5 H0 Z"/><path d="M0.3 2.2 L5 5.6 L9.7 2.2" fill="none" stroke="#fff" stroke-width="0.8"/></svg>
          hello@marlowquince.com
        </li>
        <li>
          <svg viewBox="0 0 10 10" aria-hidden="true"><circle cx="5" cy="5" r="4.6"/><path d="M0.6 5 H9.4 M5 0.4 Q2.4 5 5 9.6 M5 0.4 Q7.6 5 5 9.6" fill="none" stroke="#fff" stroke-width="0.6"/></svg>
          www.marlowquince.com
        </li>
      </ul>
    </div>

    <svg class="footer-band" viewBox="0 0 515 80" preserveAspectRatio="none" aria-hidden="true">
      <path class="band-cream" d="M0 14 Q250 -8 515 38 L515 80 L0 80 Z"/>
      <path class="band-maroon" d="M0 22 Q250 2 515 48 L515 80 L0 80 Z"/>
    </svg>
    <p class="address">00, Complex name, City, State 0025</p>
  </section>

  <section class="card card--back">
    <div class="wordmark">MARLOW &amp; QUINCE</div>
    <p class="web-address">www.marlowquince.com</p>
  </section>

</body>
</html>
```